Resident Guide for Senior Living Community

I need to create an informational magazine for residents that live in an Assisted Living community. This magazine is designed to educate the resident about the different service options and features that the community provides. I don't want to use any of the pictures in the Word Document - please use the uploaded picture instead. The final design should be both informational and elegant. The text in the word document is the actual text that needs to be used in the Resident Guide. Thanks!

Target Market(s)

Senior citizens and adult children (55 - 65 years old)

Industry/Entity Type

Assisted Living

Requirements
Must have
• Must be elegant - think Velmont Hargrove. Needs to have a lot of pictures and the logo must be used. The logo is the Plaque that says The Birch Lodge.
Nice to have
• The Word doucment is the old Resident Guide - we are looking for a refresh using the same content.
Should not have
• please do not use any pictures from the Word Document other than the Logo.

```html
<!DOCTYPE html>
<html lang="en">
<head>
<meta charset="utf-8">
<title>The Birch Lodge — Resident Guide Spread</title>
<link href="https://fonts.googleapis.com/css2?family=Lato:wght@300;400;700&display=swap" rel="stylesheet">
<style>
  :root{
    --bg:#eeeeee;
    --page:#ffffff;
    --gold:#a88a2c;
    --gold-text:#9d8236;
    --panel-top:#ad9245;
    --panel-bottom:#96793a;
    --panel-rule:#c9ad52;
    --on-gold:#fbf6e8;
  }
  *{box-sizing:border-box;margin:0;padding:0}
  html,body{width:1200px;height:1000px;overflow:hidden;background:var(--bg)}
  body{font-family:"Lato",Arial,sans-serif;position:relative}
  .spread{position:absolute;left:184px;top:164px;width:849px;height:601px;display:flex}
  .page{position:relative;width:50%;height:100%}
  .page--programs{background:var(--page)}
  .page--heritage{background:linear-gradient(160deg,var(--panel-top),var(--panel-bottom));overflow:hidden}
  .rule{position:absolute;top:26px;height:3px;background:var(--gold)}
  .page--programs .rule{left:25px;right:30px}
  .page--heritage .rule{left:28px;right:28px;height:2px;background:var(--panel-rule)}
  .page-title{position:absolute;left:28px;top:38px;font-size:17.5px;font-weight:300;color:var(--gold);white-space:nowrap}
  .page-title strong{font-weight:700}
  .page--heritage .page-title{color:var(--on-gold)}
  .program-list{position:absolute;left:43px;right:51px;top:71px;list-style:none;font-size:9.6px;font-weight:300;color:var(--gold-text);line-height:12.6px}
  .program-list>li{margin-bottom:4.4px;text-align:justify}
  .program-list>li::before{content:"• "}
  .sub-list{list-style:none;padding-left:6px}
  .sub-list li::before{content:"- "}
  .heritage-text{position:absolute;left:28px;right:28px;top:71px;font-size:9.4px;font-weight:300;color:var(--on-gold);line-height:12.8px;text-align:justify}
  .heritage-text p{margin-bottom:12.8px}
  .lounge-photo{position:absolute;left:0;top:235px;width:100%;height:366px;opacity:.35;background:radial-gradient(ellipse at 40% 40%,#d9c48a,transparent 70%)}
  .brand{position:absolute;left:132px;top:395px;width:160px;height:30px;display:flex;align-items:center;justify-content:center;font-size:14px;font-weight:700;color:var(--on-gold);white-space:nowrap}
</style>
</head>
<body>
  <div class="spread">
    <section class="page page--programs">
      <div class="rule"></div>
      <h2 class="page-title"><strong>All Levels</strong> of Health Care Programs Include</h2>
      <ul class="program-list">
        <li>Assistance with all medications as often as ordered by your physician.</li>
        <li>Coordination of outside health care providers including:</li>
        <li>Attending physician</li>
        <li>Home Health (private pay available from BirchCare)</li>
        <li>In Your Own Home Hospice Care (we own the two (2) Hospice in-patient units next door to each Birch Lodge)
          <ul class="sub-list"><li>Pharmacy</li><li>Podiatrist</li><li>Psychologist</li><li>Psychiatrist</li></ul>
        </li>
        <li>Full daily activity schedule programmed to allow each resident’s functional ability and attention level to be maximized.</li>
        <li>Laundry services three (3) times per week, or as needed.</li>
        <li>Emergency call system in each bedroom and bathroom.</li>
        <li>Our Signature “Evening Tray Room Service” when a resident is not able, or chooses not, to join us in the dining room.</li>
        <li>Housekeeping services a minimum of twice per week. More often as needed.</li>
        <li>All utilities included except telephone and cable. Units wired for service. No extra charge for wireless.</li>
        <li>Special diets available including:
          <ul class="sub-list"><li>Diabetic</li><li>Low salt</li><li>Soft mechanical Gluten free</li></ul>
        </li>
        <li>Bottled water and soft drinks to enjoy upon request.</li>
        <li>Multiple common rooms for the resident/resident family’s enjoyment:
          <ul class="sub-list">
            <li>Large living rooms with cathedral ceiling and fireplaces</li>
            <li>Screened porches overlooking wooded areas (The Birch Lodge- Cedar Hollow)</li>
            <li>Enclosed courtyards with tables, chairs and gazebos, game rooms, family rooms with fireplace, and beauty/barber salon</li>
          </ul>
        </li>
        <li>Private dining areas available for special family celebrations.</li>
        <li>A variety of nutritious snacks and goodies provided between meals from The Birch Lodge kitchens.</li>
      </ul>
    </section>

    <section class="page page--heritage">
      <div class="lounge-photo" role="img" aria-label="Gold-toned photo of an elegant living room with fireplace, armchairs and sofa"></div>
      <div class="rule"></div>
      <h2 class="page-title"><strong>Our</strong> Heritage</h2>
      <div class="heritage-text">
        <p>Each phase of life, aging or health issues carries its own challenges. So we are here with strength and support, uniquely equipped to assist you with the great majority of your loved one’s needs. And that’s among the many reasons people choose The Birch Lodge over other options in the region. We have a distinguished record of serving residents and families for thirty years. This makes us the most experienced provider of Alzheimer’s and advanced Memory Care in a residential setting in our region.</p>
        <p>Our founder’s father, Dr. Edwin R. Birch Jr. was the inspiration for The Birch Lodge. He was a Doctor of Public Health and a nationally prominent physician, educator and pharmaceutical research executive.</p>
        <p>His exemplary inspiration, dedication and lifelong pursuit of medical answers for some of humanity’s most destructive diseases, along with his personal struggle with Alzheimer’s over 17 years, is the legacy of The Birch Lodge.</p>
      </div>
      <div class="brand">The Birch Lodge</div>
    </section>
  </div>
</body>
</html>
```